larkforge website

commerce website to sell cookeries, brackets, mailboxes and to show off homes built. Modern Steel in design see marlo cycles web page to be like: https://www.marlocycles-demo.com/en/ sorry its bright nest hosting word press divi

must be able to add products to page

Target Market(s)

mainly western states of U.S.

Industry/Entity Type

Building Product

Coding

Coded - Design and coding required

Number of Pages Required

3 page

Font styles to use
Sans Serif

Colors

Designer to choose colors to be used in the design.

Requirements
Must have
• customers to be able to order products from page
• bright nest hosting word press divi

```html
<!DOCTYPE html>
<html lang="en">
<head>
<meta charset="utf-8">
<title>Lark Forge — Steel Goods</title>
<link href="https://fonts.googleapis.com/css2?family=Montserrat:ital,wght@0,300;0,400;0,500;0,600;0,700;0,800;1,400&display=swap" rel="stylesheet">
<style>
:root{
  --slate:#56648f;
  --slate-dark:#46527a;
  --ink:#222;
  --text:#555;
  --muted:#8a8a8a;
  --green:#3c9a3c;
  --red:#d92b2b;
  --gold:#e0a526;
  --nav:#1b1b1b;
  --line:#e3e3e3;
}
*{box-sizing:border-box;margin:0;padding:0}
html,body{width:1200px;height:3426px;overflow:hidden}
body{font-family:'Montserrat',sans-serif;color:var(--ink);background:#fff}
.page{position:relative;width:1200px;height:3426px;overflow:hidden}
.abs{position:absolute}

/* header */
.topbar{left:0;top:0;width:1200px;height:38px;background:var(--slate);color:#fff;font-size:14px}
.topbar .call{left:143px;top:9px;display:flex;align-items:center;gap:8px;font-weight:500}
.topbar .call b{font-weight:700;font-size:17px}
.topbar .util{right:145px;top:11px;font-size:13px;display:flex;gap:14px;align-items:center}
.topbar .soc{display:flex;gap:6px}
.topbar .soc i{width:12px;height:12px;background:#fff;border-radius:2px;display:block}
.navbar{left:0;top:38px;width:1200px;height:94px;background:rgba(20,20,20,.92);z-index:2}
.nav a{color:#fff;text-decoration:none;font-size:14px;font-weight:500;position:absolute;top:38px;letter-spacing:.3px}
.brand-disc{left:480px;top:-60px;width:240px;height:210px;border-radius:0 0 120px 120px;background:var(--slate);z-index:3}
.brand-name{left:480px;top:68px;width:240px;text-align:center;color:#fff;font-size:29px;font-weight:500;letter-spacing:1px;z-index:4}
.brand-mark{left:585px;top:14px;width:30px;height:30px;border:3px solid #fff;border-radius:50%;z-index:4}
.icon-btn{width:32px;height:32px;border:2px solid #fff;border-radius:50%;top:69px;z-index:3}

/* hero */
.hero{left:0;top:0;width:1200px;height:740px;clip-path:polygon(0 0,100% 0,100% 607px,50% 740px,0 607px);
  background:radial-gradient(ellipse at 50% 40%,#3a3a36 0%,#2b2d2a 28%,transparent 45%),linear-gradient(180deg,#4a6b2e 0%,#5f8a3a 45%,#6c9242 100%)}
.hero-title{left:0;top:270px;width:1200px;text-align:center;color:#fff;font-size:92px;letter-spacing:1px;line-height:1}
.hero-title b{font-weight:800}.hero-title span{font-weight:300}
.hero-sub{left:0;top:388px;width:1200px;text-align:center;color:#fff;font-size:24px;font-weight:500}
.btn{background:var(--slate);color:#fff;font-weight:700;border-radius:30px;text-align:center;text-transform:uppercase}
.hero-btn{left:509px;top:458px;width:183px;height:54px;line-height:54px;font-size:14px}
.dots{left:1121px;top:361px;display:flex;flex-direction:column;gap:8px}
.dots i{width:13px;height:13px;border-radius:50%;background:#fff;display:block}
.dots i.on{background:var(--slate)}

/* section heads */
.sec-head{left:142px;font-size:32px;letter-spacing:.5px}
.sec-head b{font-weight:700}.sec-head span{font-weight:300;color:var(--slate)}
.sec-rule{height:1px;background:var(--line)}
.arrow{width:24px;height:24px;border-radius:50%;border:1px solid #ccc;background:#f4f4f4;font-size:13px;line-height:22px;text-align:center;color:#333}

/* product card */
.card{width:216px;height:357px;border:1px solid #e6e6e6;background:#fff}
.card .ph{position:absolute;left:4px;top:4px;width:206px;height:140px}
.card .name{position:absolute;left:15px;top:163px;font-size:14px;font-weight:700}
.card .price{position:absolute;left:15px;top:193px;font-size:15px;color:var(--muted);font-weight:400}
.card .price s{color:#bbb;font-size:14px;margin:0 12px 0 2px}
.card .price b{color:var(--slate-dark);font-weight:600;font-size:16px}
.card .del{position:absolute;left:15px;top:230px;font-size:10px;color:#444}
.card .del em{font-style:normal;margin-left:12px}
.in{color:var(--green)}.out{color:var(--red)}
.card .stars{position:absolute;left:15px;top:250px;font-size:11px;color:var(--gold);letter-spacing:1px}
.card .meta{position:absolute;left:15px;top:273px;font-size:10px;color:#444}
.card .cart{position:absolute;left:15px;top:305px;width:122px;height:37px;line-height:37px;font-size:12px}

/* about */
.about-bg{left:0;top:1378px;width:1200px;height:567px;clip-path:polygon(0 122px,50% 0,100% 122px,100% 100%,0 100%);
  background:linear-gradient(100deg,#d9d9da 0%,#f2f2f3 35%,#e4e4e6 65%,#f3f3f4 100%)}
.about-mark{left:20px;top:1560px;width:600px;text-align:center;font-size:84px;font-weight:800;color:#3b3b3b;letter-spacing:2px}
.about-title{left:648px;top:1542px;font-size:32px}
.about-title b{font-weight:700}.about-title span{font-weight:300;color:var(--slate)}
.about-text{left:648px;top:1604px;width:410px;font-size:14px;line-height:29.6px;color:var(--text);font-weight:400}
.about-btn{left:648px;top:1808px;width:160px;height:48px;line-height:48px;font-size:14px}

/* reviews */
.rev-bg{left:0;top:2610px;width:1200px;height:410px;clip-path:polygon(0 80px,50% 0,100% 80px,100% 100%,0 100%);
  background:linear-gradient(180deg,#6a78a2 0%,#5b6895 40%,#4f5c88 100%)}
.rev-edge{left:0;top:2600px;width:1200px;height:90px}
.rev-knob{left:566px;top:2574px;width:68px;height:68px;border-radius:50%;background:#fff}
.rev-head{left:0;top:2706px;width:1200px;text-align:center;color:#fff;font-size:32px}
.rev-head b{font-weight:700}.rev-head span{font-weight:300}
.review{width:320px;color:#fff}
.review .face{position:absolute;left:0;top:0;width:70px;height:70px;border-radius:50%;border:3px solid #fff;background:linear-gradient(160deg,#d8d2cc,#9e958f)}
.review .q{position:absolute;left:87px;top:12px;width:220px;font-size:13px;font-style:italic;line-height:21px}
.review .q b{font-size:18px;font-weight:800;margin-right:8px}
.review .who{position:absolute;left:87px;top:95px;font-size:10px;font-weight:700}
.review .role{position:absolute;left:87px;top:110px;font-size:10px;font-weight:700;white-space:nowrap}
.review .st{position:absolute;left:87px;top:133px;font-size:17px;color:#f2c20f;letter-spacing:3px}
.rev-arrow{width:34px;height:34px;border-radius:50%;border:1px solid #fff;color:#fff;text-align:center;line-height:30px;font-size:18px;top:2838px}

/* mailing */
.mail{left:0;top:3020px;width:1200px;height:108px;background:#0d0d0d}
.mail h3{position:absolute;left:143px;top:36px;color:#fff;font-size:30px;font-weight:400;letter-spacing:.5px}
.mail .field{position:absolute;left:535px;top:37px;width:384px;height:37px;background:#fff;font-size:12px;color:#555;padding:11px 20px}
.mail .sign{position:absolute;left:928px;top:37px;width:127px;height:37px;background:#3b4d86;color:#fff;font-size:15px;font-weight:700;text-align:center;line-height:37px}

/* footer */
.fcol h4{font-size:14px;font-weight:500;color:var(--slate);margin-bottom:15px;letter-spacing:.3px}
.fcol p{font-size:12px;color:#333;line-height:23px}
.fc-row{display:flex;gap:14px;font-size:12px;color:#333;line-height:19px;margin-bottom:12px}
.fc-row i{width:16px;height:14px;flex:none;margin-top:2px}
.soc-dots{display:flex;gap:8px;margin-top:4px}
.soc-dots i{width:26px;height:26px;border-radius:50%;display:block}
.totop{left:1110px;top:3308px;width:44px;height:44px;border-radius:50%;border:2px solid var(--slate);color:var(--slate);text-align:center;font-size:22px;line-height:38px;font-weight:700}
.foot-rule{left:143px;top:3353px;width:912px;height:1px;background:var(--line)}
.pay{top:3380px;width:30px;height:20px;border-radius:2px}
.copy{right:145px;top:3384px;font-size:12px;color:#333}
</style>
</head>
<body>
<div class="page">

  <!-- hero -->
  <div class="abs hero" role="img" aria-label="Steel fire pit with mesh dome cover burning on a green lawn"></div>
  <svg class="abs" style="left:0;top:590px" width="1200" height="160" viewBox="0 590 1200 160">
    <polygon points="120,640 600,740 1080,640 1080,652 600,752 120,652" fill="#56648f"/>
  </svg>
  <div class="abs hero-title"><b>LARK</b> <span>FORGE</span></div>
  <div class="abs hero-sub">Lorem ipsum dolor sit amet consectetur adipiscing elit</div>
  <div class="abs btn hero-btn">View Products</div>
  <div class="abs dots"><i></i><i></i><i class="on"></i><i></i><i></i></div>

  <!-- header -->
  <div class="abs topbar">
    <div class="abs call">
      <svg width="26" height="26" viewBox="0 0 26 26"><circle cx="13" cy="13" r="12" fill="none" stroke="#fff" stroke-width="1.6"/><path d="M9 7l3 3-2 2c1 2 2 3 4 4l2-2 3 3-2 2c-5 0-10-5-10-10z" fill="#fff"/></svg>
      <span>CALL US : <b>1 888 888 8888</b></span>
    </div>
    <div class="abs util">
      <span>&#9679; Location |</span>
      <span>&#9675; Search</span>
      <span class="soc"><i></i><i></i><i></i><i></i></span>
    </div>
  </div>
  <div class="abs navbar">
    <div class="nav">
      <a style="left:143px">HOME</a>
      <a style="left:221px">ABOUT US</a>
      <a style="left:327px">PRODUCTS</a>
      <a style="left:805px">NEWS</a>
      <a style="left:881px">CONTACT</a>
    </div>
  </div>
  <div class="abs brand-disc"></div>
  <div class="abs brand-mark"></div>
  <div class="abs brand-name">LARK FORGE</div>
  <div class="abs icon-btn" style="left:971px"></div>
  <svg class="abs" style="left:1016px;top:70px;z-index:3" width="38" height="30" viewBox="0 0 38 30"><path d="M2 3h6l5 16h18l4-12H11" fill="none" stroke="#fff" stroke-width="2.4"/><circle cx="15" cy="25" r="3" fill="#fff"/><circle cx="28" cy="25" r="3" fill="#fff"/></svg>

  <!-- featured -->
  <div class="abs sec-head" style="top:830px"><b>FEATURED</b> <span>PRODUCTS</span></div>
  <div class="abs sec-rule" style="left:537px;top:850px;width:440px"></div>
  <div class="abs arrow" style="left:998px;top:838px">&#8249;</div>
  <div class="abs arrow" style="left:1029px;top:838px">&#8250;</div>

  <div class="abs card" style="left:143px;top:925px">
    <div class="ph" role="img" aria-label="Round kettle grill with chrome grate" style="background:linear-gradient(160deg,#6d7a8a,#1d2229 70%)"></div>
    <div class="name">PRODUCT NAME</div>
    <div class="price">Price : <s>$56.98</s><b>$36.98</b></div>
    <div class="del">FREE Delivery. Details <em class="in">In Stock</em></div>
    <div class="stars">★★★★★</div>
    <div class="meta">( 14 ratings | 10+ answered questions)</div>
    <div class="btn cart">Add to cart</div>
  </div>
  <div class="abs card" style="left:375px;top:925px">
    <div class="ph" role="img" aria-label="Fire pit with flames on grass" style="background:linear-gradient(180deg,#5d8a3c,#d8802a 45%,#2a2a2a 80%)"></div>
    <div class="name">PRODUCT NAME</div>
    <div class="price">Price : <s>$56.98</s><b>$36.98</b></div>
    <div class="del">FREE Delivery. Details <em class="out">No Stock</em></div>
    <div class="stars">★★★★★</div>
    <div class="meta">( 14 ratings | 10+ answered questions)</div>
    <div class="btn cart">Add to cart</div>
  </div>
  <div class="abs card" style="left:607px;top:925px">
    <div class="ph" role="img" aria-label="Square cast iron grill pan on wooden table" style="background:radial-gradient(circle at 50% 50%,#222 0 38%,#b48a63 40%,#c9a07a 100%)"></div>
    <div class="name">PRODUCT NAME</div>
    <div class="price">Price : <s>$56.98</s><b>$36.98</b></div>
    <div class="del">FREE Delivery. Details <em class="in">In Stock</em></div>
    <div class="stars">★★★★★</div>
    <div class="meta">( 14 ratings | 10+ answered questions)</div>
    <div class="btn cart">Add to cart</div>
  </div>
  <div class="abs card" style="left:839px;top:925px">
    <div class="ph" role="img" aria-label="Close-up of a round steel cooking grate" style="background:linear-gradient(140deg,#2a3340,#8a98aa 50%,#1e242c)"></div>
    <div class="name">PRODUCT NAME</div>
    <div class="price">Price : <s>$56.98</s><b>$36.98</b></div>
    <div class="del">FREE Delivery. Details <em class="in">In Stock</em></div>
    <div class="stars">★★★★★</div>
    <div class="meta">( 14 ratings | 10+ answered questions)</div>
    <div class="btn cart">Add to cart</div>
  </div>

  <!-- about -->
  <div class="abs about-bg"></div>
  <div class="abs about-mark">LARK FORGE</div>
  <div class="abs about-title"><b>ABOUT</b> <span>LARK FORGE</span></div>
  <p class="abs about-text">Lorem ipsum dolor sit amet, consectetur adipiscing elit, sed do eiusmod tempor incididunt ut labore et dolore magna aliquauis ipsum suspendisse ultrices grisorem ipsum dolor sit amet, consectetur adipiscing elit, sed do eiusmod tempor incididunt ut labore et dolore maultrices grisus commodo viverra maecenas accumsamaecenas vel facilisis.</p>
  <div class="abs btn about-btn">Read More</div>

  <!-- best selling -->
  <div class="abs sec-head" style="top:2053px"><b>BEST</b> <span>SELLING</span></div>
  <div class="abs sec-rule" style="left:398px;top:2073px;width:578px"></div>
  <div class="abs arrow" style="left:998px;top:2061px">&#8249;</div>
  <div class="abs arrow" style="left:1029px;top:2061px">&#8250;</div>

  <div class="abs card" style="left:143px;top:2149px">
    <div class="ph" role="img" aria-label="Portable grill with flames on grass" style="background:linear-gradient(180deg,#5f8d3e,#e0892c 50%,#3b2a22)"></div>
    <div class="name">PRODUCT NAME</div>
    <div class="price">Price : <s>$56.98</s><b>$36.98</b></div>
    <div class="del">FREE Delivery. Details <em class="in">In Stock</em></div>
    <div class="stars">★★★★★</div>
    <div class="meta">( 14 ratings | 10+ answered questions)</div>
    <div class="btn cart">Add to cart</div>
  </div>
  <div class="abs card" style="left:375px;top:2149px">
    <div class="ph" role="img" aria-label="Long charcoal brazier with glowing coals" style="background:linear-gradient(180deg,#3b3838,#1c1c1c 45%,#d4722a 70%,#2a2422)"></div>
    <div class="name">PRODUCT NAME</div>
    <div class="price">Price : <s>$56.98</s><b>$36.98</b></div>
    <div class="del">FREE Delivery. Details <em class="in">In Stock</em></div>
    <div class="stars">★★★★★</div>
    <div class="meta">( 14 ratings | 10+ answered questions)</div>
    <div class="btn cart">Add to cart</div>
  </div>
  <div class="abs card" style="left:607px;top:2149px">
    <div class="ph" role="img" aria-label="Kettle grill standing on a lawn" style="background:linear-gradient(180deg,#4f6a35,#7aa24a 55%,#6e9a44)"></div>
    <div class="name">PRODUCT NAME</div>
    <div class="price">Price : <s>$56.98</s><b>$36.98</b></div>
    <div class="del">FREE Delivery. Details <em class="out">No Stock</em></div>
    <div class="stars">★★★★★</div>
    <div class="meta">( 14 ratings | 10+ answered questions)</div>
    <div class="btn cart">Add to cart</div>
  </div>
  <div class="abs card" style="left:839px;top:2149px">
    <div class="ph" role="img" aria-label="Fire pit with large flames" style="background:linear-gradient(180deg,#2a2622,#e07a22 55%,#1e1a18)"></div>
    <div class="name">PRODUCT NAME</div>
    <div class="price">Price : <s>$56.98</s><b>$36.98</b></div>
    <div class="del">FREE Delivery. Details <em class="in">In Stock</em></div>
    <div class="stars">★★★★★</div>
    <div class="meta">( 14 ratings | 10+ answered questions)</div>
    <div class="btn cart">Add to cart</div>
  </div>

  <!-- reviews -->
  <svg class="abs rev-edge" viewBox="0 2600 1200 90" width="1200" height="90">
    <polygon points="0,2690 600,2616 1200,2690 1200,2684 600,2608 0,2684" fill="#cfcfd2"/>
  </svg>
  <div class="abs rev-bg"></div>
  <div class="abs rev-knob"></div>
  <div class="abs rev-head"><b>CLIENT</b> <span>REVIEWS</span></div>
  <div class="abs rev-arrow" style="left:66px">&#8249;</div>
  <div class="abs rev-arrow" style="left:1099px">&#8250;</div>

  <div class="abs review" style="left:130px;top:2783px">
    <div class="face" role="img" aria-label="Reviewer portrait"></div>
    <div class="q"><b>"</b>At vero eos et accusamus et iustodio dignissimos ducimus qui blanditiipraesnt ium voluptatum</div>
    <div class="who">MAREN HOLT</div>
    <div class="role">Financial Services Professional</div>
    <div class="st">★★★★☆</div>
  </div>
  <div class="abs review" style="left:457px;top:2783px">
    <div class="face" role="img" aria-label="Reviewer portrait"></div>
    <div class="q"><b>"</b>At vero eos et accusamus et iustodio dignissimos ducimus qui blanditiipraesnt ium volupleniti</div>
    <div class="who">TOBIAS R. VANCE</div>
    <div class="role">National Urban Fellow at the Houston</div>
    <div class="st">★★★★☆</div>
  </div>
  <div class="abs review" style="left:780px;top:2783px">
    <div class="face" role="img" aria-label="Reviewer portrait"></div>
    <div class="q"><b>"</b>At vero eos et accusamus et iustodio dignissimos ducimus qui blanditiipraesnt ium voluptatum</div>
    <div class="who">ELSIE BRANDT</div>
    <div class="role">Creative Strategist | Entrepreneur &amp; Upcoming</div>
    <div class="st">★★★★☆</div>
  </div>

  <!-- mailing list -->
  <div class="abs mail">
    <h3>JOIN OUR MAILING LIST</h3>
    <div class="field">Enter Email</div>
    <div class="sign">SIGN UP</div>
  </div>

  <!-- footer -->
  <div class="abs fcol" style="left:145px;top:3182px;width:220px">
    <h4>CONTACT US</h4>
    <div class="fc-row"><svg width="16" height="14" viewBox="0 0 16 14"><path d="M8 1L1 7h2v6h4V9h2v4h4V7h2z" fill="#444"/></svg><span>134,Sed ut perspiciatis unde<br>omnis iste natus erro..</span></div>
    <div class="fc-row"><svg width="16" height="14" viewBox="0 0 16 14"><path d="M3 1l3 3-2 2c1 2 2 3 4 4l2-2 3 3-2 2C6 13 1 8 1 3z" fill="#444"/></svg><span>Call us : 1 888 888 8888</span></div>
    <div class="fc-row"><svg width="16" height="14" viewBox="0 0 16 14"><rect x="1" y="2" width="14" height="10" fill="#444"/><path d="M1 2l7 6 7-6" fill="none" stroke="#fff" stroke-width="1.2"/></svg><span>Email : info@larkforge.com</span></div>
  </div>
  <div class="abs fcol" style="left:410px;top:3182px">
    <h4>ACCOUNTS &amp; ORDERS</h4>
    <p>Gift Certificates<br>Wishlist<br>Login or Sign up<br>Shipping &amp; Returns<br>Sitemap</p>
  </div>
  <div class="abs fcol" style="left:651px;top:3182px">
    <h4>QUICK LINKS</h4>
    <p>Why Choose us<br>Shipping &amp; returns<br>Contact us<br>Blog</p>
  </div>
  <div class="abs fcol" style="left:857px;top:3182px">
    <h4>RECENT BLOG POSTS</h4>
    <p>Your first blog Post!</p>
    <h4 style="margin-top:22px">CONNECT WITH US</h4>
    <div class="soc-dots"><i style="background:#2c4a8c"></i><i style="background:#2aa3ef"></i><i style="background:#d13b2e"></i><i style="background:#a88a5c"></i></div>
  </div>
  <div class="abs totop">&#8593;</div>
  <div class="abs foot-rule"></div>
  <div class="abs pay" style="left:145px;background:#d9a23a"></div>
  <div class="abs pay" style="left:184px;background:#2a5aa8"></div>
  <div class="abs pay" style="left:223px;background:#3f86c8"></div>
  <div class="abs pay" style="left:262px;background:#e8a24a"></div>
  <div class="abs copy">© copyright 2020 Lark Forge All Rights Reserved &nbsp;|&nbsp; Privacy policy</div>

</div>
</body>
</html>
```